Website Design for The Elder Nook

Please design and code a new website.
Here are the sites I like best:
http://www.voyaglint.com/alternate/
http://www.wheelgiftbay.org
Please make it similar but look at the competitor site (below) for images and wording. This is NOT a car donation site. It's a senior lead placement site like https://www.kinhavenfinder.com. I just like this sites above as a lead generation sites.
Competitor site:
https://www.kinhavenfinder.com (use ideas / verbiage from this site)
Updates
Competitor site:
Coding
Coded - Design and coding required
Number of Pages Required
1 page
Look and feel
Each slider illustrates characteristics of the customer's brand and the style your logo design should communicate.

```html
<!DOCTYPE html>
<html lang="en">
<head>
<meta charset="utf-8">
<title>The Elder Nook</title>
<link href="https://fonts.googleapis.com/css2?family=Lora:ital,wght@0,400;0,500;1,400&family=Montserrat:wght@600&display=swap" rel="stylesheet">
<style>
:root{
  --page-bg:#e4fafa;
  --white:#ffffff;
  --brown:#5b3520;
  --teal:#1aa79a;
  --teal-dark:#14998d;
  --grey-text:#6d6d6d;
  --soft-band:#f4f3f1;
  --star:#f26a1b;
  --star-off:#b9b9b9;
}
*{margin:0;padding:0;box-sizing:border-box}
html,body{width:1200px;height:2760px;overflow:hidden;background:var(--page-bg)}
body{font-family:'Lora',serif;position:relative}
.page{position:absolute;left:150px;top:0;width:900px;height:2760px;background:var(--white)}
.abs{position:absolute}
.center{left:0;width:900px;text-align:center}

.brand{top:30px;font-size:43px;color:var(--brown);font-weight:400;font-family:'Lora',serif}
.main-nav{top:120px;left:0;width:900px;height:55px;background:var(--brown);display:flex;justify-content:center;align-items:center;gap:32px}
.main-nav a{font-family:'Montserrat',sans-serif;font-weight:600;font-size:10.5px;color:var(--white);text-decoration:none;letter-spacing:.2px}

.hero{top:175px;left:0;width:900px;height:482px;background:linear-gradient(100deg,#d9ecf8 0%,#bfe0f4 35%,#e9e2d6 60%,#f1ece4 100%)}
.hero-kicker{left:28px;top:170px;font-size:26px;color:#2f2520}
.hero-title{left:28px;top:208px;font-size:36px;color:var(--teal);font-style:italic}
.hero-title span{font-style:normal}
.btn-solid{left:32px;top:280px;width:129px;height:41px;background:var(--teal);color:var(--white);font-style:italic;font-size:16px;display:flex;align-items:center;justify-content:center}
.dots{left:41px;top:451px;display:flex;gap:4px}
.dots i{width:12px;height:12px;border-radius:50%;background:#4a4a4a;display:block}
.dots i.on{background:var(--teal)}

.support-title{top:696px;font-size:34px;color:#3a2a20}
.support-sub{top:743px;font-size:20px;color:var(--teal)}
.support-text{top:786px;left:150px;width:600px;text-align:center;font-size:13.5px;line-height:27px;font-style:italic;color:var(--grey-text)}
.call{top:860px;font-size:32px;font-style:italic;color:var(--brown)}

.feature{width:200px;text-align:center}
.feature .disc{width:116px;height:116px;border-radius:50%;margin:0 auto;display:flex;align-items:center;justify-content:center}
.feature .label{margin-top:13px;font-size:18px;line-height:24px;font-style:italic}
.teal-bg{background:var(--teal)} .brown-bg{background:var(--brown)}
.teal-tx{color:var(--teal)} .brown-tx{color:var(--brown)}

.advisor-band{top:1167px;left:0;width:900px;height:345px;background:var(--teal)}
.advisor-title{top:44px;font-size:27px;color:var(--white)}
.advisor-sub{top:88px;font-size:17px;font-style:italic;color:var(--white)}
.perk{width:240px;text-align:center;top:145px}
.perk .ring{width:101px;height:101px;border-radius:50%;background:var(--white);border:3px solid var(--white);box-shadow:inset 0 0 0 3px var(--teal);margin:0 auto;display:flex;align-items:center;justify-content:center}
.perk .label{margin-top:20px;font-size:15px;line-height:23px;font-style:italic;color:var(--white)}

.round-photo{width:310px;height:310px;border-radius:50%;border:4px solid #e8e8e8}
.photo-couple{background:radial-gradient(circle at 45% 40%,#f2e6d6 0%,#d8b98d 45%,#a8854f 100%)}
.photo-care{background:radial-gradient(circle at 55% 45%,#f4f1ee 0%,#e3ddd8 50%,#9bb4d8 100%)}
.section-head{font-size:26px;color:var(--brown)}
.rule{height:3px;width:91px;background:var(--teal)}
.body-copy{font-family:Arial,Helvetica,sans-serif;font-size:11.5px;line-height:23.5px;color:var(--grey-text);width:360px}
.btn-line{width:124px;height:42px;border:1px solid var(--teal);color:var(--teal);font-size:13px;display:flex;align-items:center;justify-content:center}

.reviews{top:2272px;left:0;width:900px;height:251px;background:var(--soft-band)}
.avatar{width:114px;height:114px;border-radius:50%;border:3px solid #ddd;background:radial-gradient(circle at 50% 45%,#e8c2a3 0%,#b9876a 55%,#6d6f72 100%)}
.divider{width:1px;height:120px;background:#cfcfcf}
.quote-mark{font-size:30px;line-height:20px;color:var(--star);font-family:Georgia,serif;font-weight:700}
.review-text{font-family:Arial,Helvetica,sans-serif;font-size:10.3px;line-height:22.5px;color:#555;width:272px}
.review-name{font-family:'Lora',serif;font-size:13px;color:#555}
.stars{font-size:12px;letter-spacing:1px;color:var(--star)}
.stars b{color:var(--star-off);font-weight:400}

.site-footer{top:2523px;left:0;width:900px;height:237px;background:var(--brown)}
.footer-brand{top:24px;font-size:38px;color:var(--white)}
.footer-rule{left:25px;top:95px;width:850px;height:1px;background:rgba(255,255,255,.2)}
.social{top:116px;width:52px;height:52px;border-radius:50%;border:1px solid rgba(255,255,255,.55);display:flex;align-items:center;justify-content:center}
.copyright{top:196px;font-family:Arial,Helvetica,sans-serif;font-size:11px;color:var(--white)}
</style>
</head>
<body>
<div class="page">
  <div class="abs center brand">The Elder Nook</div>
  <nav class="abs main-nav">
    <a>ASSISTED LIVING</a><a>MEMORY CARE</a><a>NURSING HOMES</a><a>MORE LIVING OPTIONS</a><a>PLANNING &amp; ADVICE</a><a>HOW OUR SERVICE WORKS</a>
  </nav>

  <section class="abs hero" role="img" aria-label="Smiling senior couple embracing outdoors under a blue sky">
    <div class="abs hero-kicker">YOU KNOW YOUR FAMILY</div>
    <div class="abs hero-title">We know <span>SENIOR LIVING</span></div>
    <div class="abs btn-solid">Read More</div>
    <div class="abs dots"><i></i><i class="on"></i><i></i></div>
  </section>

  <h2 class="abs center support-title" style="font-weight:400">The support you need to</h2>
  <div class="abs center support-sub">make the RIGHT CHOICE</div>
  <p class="abs support-text">Sed ut perspiciatis unde omnis iste natus error sit voluptatem accusantium doloremque laudan inventore veritatis et quasi architecto beatae vitae dicta sunt explicabo.</p>
  <div class="abs center call">Call Us : 000-555-0187</div>

  <div class="abs feature" style="left:26px;top:951px">
    <div class="disc teal-bg"><svg width="56" height="56" viewBox="0 0 56 56" fill="none" stroke="#fff" stroke-width="2"><circle cx="28" cy="10" r="5"/><path d="M28 15v10M12 25h32M12 25v8M44 25v8M28 25v8"/><circle cx="12" cy="38" r="4"/><circle cx="28" cy="38" r="4"/><circle cx="44" cy="38" r="4"/><path d="M6 50l6-8 6 8M22 50l6-8 6 8M38 50l6-8 6 8"/></svg></div>
    <div class="label teal-tx">Dedicated<br>Local Advisor</div>
  </div>
  <div class="abs feature" style="left:244px;top:951px">
    <div class="disc brown-bg"><svg width="56" height="56" viewBox="0 0 56 56" fill="none" stroke="#fff" stroke-width="2.2"><circle cx="28" cy="28" r="20"/><path d="M34 20c-2-3-12-3-12 2s12 3 12 9-10 5-12 2M28 14v28"/></svg></div>
    <div class="label brown-tx">Full details &amp;<br>pricing</div>
  </div>
  <div class="abs feature" style="left:462px;top:951px">
    <div class="disc teal-bg"><svg width="58" height="58" viewBox="0 0 58 58" fill="none" stroke="#fff" stroke-width="2"><rect x="6" y="10" width="38" height="34" rx="3"/><path d="M6 19h38M14 6v8M36 6v8"/><circle cx="42" cy="42" r="11" fill="#1aa79a"/><path d="M42 36v6h5"/></svg></div>
    <div class="label teal-tx">Help scheduling<br>tours</div>
  </div>
  <div class="abs feature" style="left:680px;top:951px">
    <div class="disc brown-bg"><svg width="58" height="58" viewBox="0 0 58 58" fill="none" stroke="#fff" stroke-width="2"><circle cx="29" cy="18" r="7"/><circle cx="29" cy="18" r="2.5"/><path d="M8 26v14l8 8h8v-10l-8-8M50 26v14l-8 8h-8v-10l8-8"/></svg></div>
    <div class="label brown-tx">Move in<br>support</div>
  </div>

  <section class="abs advisor-band">
    <div class="abs center advisor-title">Your LOCAL ADVISOR informs. You decide</div>
    <div class="abs center advisor-sub">Over 400 senior advisors across the U.S. and Canada are ready to help your family with</div>
    <div class="abs perk" style="left:43px">
      <div class="ring"><svg width="50" height="50" viewBox="0 0 50 50" fill="none" stroke="#1aa79a" stroke-width="2"><path d="M18 30c-4-3-6-7-6-11a13 13 0 0126 0c0 4-2 8-6 11v5H18z"/><path d="M19 39h12M20 43h10M25 35V24l-3-3M25 24l3-3M25 1v3M6 8l2 2M44 8l-2 2"/></svg></div>
      <div class="label">Insider's tips for the area<br>near you</div>
    </div>
    <div class="abs perk" style="left:325px">
      <div class="ring"><svg width="52" height="52" viewBox="0 0 52 52" fill="none" stroke="#1aa79a" stroke-width="2.4"><path d="M18 10h28v20h-6v6l-6-6H18z"/><path d="M6 18h24v20H14l-6 6v-6H6z" fill="#fff"/></svg></div>
      <div class="label">Advice tailored to your<br>unique situation</div>
    </div>
    <div class="abs perk" style="left:616px">
      <div class="ring"><svg width="50" height="50" viewBox="0 0 50 50" fill="none" stroke="#1aa79a" stroke-width="2.2"><circle cx="25" cy="28" r="17"/><path d="M21 5h8M25 5v6M38 13l3-3M25 28l-6-7"/><circle cx="25" cy="28" r="2"/></svg></div>
      <div class="label">Time saving know-how and<br>resources</div>
    </div>
  </section>

  <div class="abs round-photo photo-couple" style="left:95px;top:1558px" role="img" aria-label="Happy senior couple hugging outdoors in autumn"></div>
  <h3 class="abs section-head" style="left:455px;top:1578px;font-weight:400">INDEPENDENT LIVING</h3>
  <div class="abs rule" style="left:455px;top:1620px"></div>
  <p class="abs body-copy" style="left:456px;top:1644px">Sed ut perspiciatis unde omnis iste natus error sit voluptatem accusantium doloremque laudantium, totam rem aperiam, eaque ipsa quae ab illo inventore veritatis et quasi architecto beatae vitae dicta sunt explicabo. Nemo enim ipsam voluptatem quia voluptas sit aspernatur aut dolores eos qui ratione voluptatem sequi nesciunt.</p>
  <div class="abs btn-line" style="left:456px;top:1787px">READ MORE</div>

  <h3 class="abs section-head" style="left:94px;top:1940px;font-weight:400">CARE HOMES</h3>
  <div class="abs rule" style="left:96px;top:1982px"></div>
  <p class="abs body-copy" style="left:96px;top:2006px">Sed ut perspiciatis unde omnis iste natus error sit voluptatem accusantium doloremque laudantium, totam rem aperiam, eaque ipsa quae ab illo inventore veritatis et quasi architecto beatae vitae dicta sunt explicabo. Nemo enim ipsam voluptatem quia voluptas sit aspernatur aut dolores eos qui ratione voluptatem sequi nesciunt.</p>
  <div class="abs btn-line" style="left:96px;top:2149px">READ MORE</div>
  <div class="abs round-photo photo-care" style="left:493px;top:1920px" role="img" aria-label="Smiling elderly woman with a caring nurse"></div>

  <section class="abs reviews" role="group" aria-label="Client reviews">
    <div class="abs avatar" style="left:20px;top:65px" role="img" aria-label="Portrait of a smiling client"></div>
    <div class="abs divider" style="left:149px;top:62px"></div>
    <div class="abs quote-mark" style="left:169px;top:78px">&ldquo;</div>
    <p class="abs review-text" style="left:169px;top:68px;text-indent:26px">Sed ut perspiciatis unde omnis iste natus error sit voluptatem accusantium doloremque laudantium, totam rem aperiam, eaque ipsa quae ab illo inventore veritatis et quasi architecto beatae vitae dicta sunt explicabo.</p>
    <div class="abs review-name" style="left:169px;top:176px">- DARYL WEST</div>
    <div class="abs stars" style="left:368px;top:176px">★★★<b>★★</b></div>

    <div class="abs avatar" style="left:464px;top:65px" role="img" aria-label="Portrait of a smiling client with glasses"></div>
    <div class="abs divider" style="left:591px;top:62px"></div>
    <div class="abs quote-mark" style="left:612px;top:78px">&ldquo;</div>
    <p class="abs review-text" style="left:612px;top:68px;text-indent:26px">Sed ut perspiciatis unde omnis iste natus error sit voluptatem accusantium doloremque laudantium, totam rem aperiam, eaque ipsa quae ab illo inventore veritatis et quasi architecto beatae vitae dicta sunt explicabo.</p>
    <div class="abs review-name" style="left:612px;top:176px">-&nbsp; DARYL WEST</div>
    <div class="abs stars" style="left:811px;top:176px">★★★<b>★★</b></div>
  </section>

  <footer class="abs site-footer">
    <div class="abs center footer-brand">The Elder Nook</div>
    <div class="abs footer-rule"></div>
    <div class="abs social" style="left:263px" aria-label="Share"><svg width="16" height="16" viewBox="0 0 16 16" fill="none" stroke="#fff" stroke-width="1.4"><circle cx="12" cy="3" r="2"/><circle cx="4" cy="8" r="2"/><circle cx="12" cy="13" r="2"/><path d="M6 7l4-3M6 9l4 3"/></svg></div>
    <div class="abs social" style="left:326px" aria-label="Chat"><svg width="16" height="14" viewBox="0 0 16 14" fill="none" stroke="#fff" stroke-width="1.4"><path d="M1 1h14v9H6l-4 3v-3H1z"/></svg></div>
    <div class="abs social" style="left:389px" aria-label="Website"><svg width="16" height="16" viewBox="0 0 16 16" fill="none" stroke="#fff" stroke-width="1.3"><circle cx="8" cy="8" r="7"/><path d="M1 8h14M8 1c-3 4-3 10 0 14M8 1c3 4 3 10 0 14"/></svg></div>
    <div class="abs social" style="left:453px" aria-label="Link"><svg width="16" height="16" viewBox="0 0 16 16" fill="none" stroke="#fff" stroke-width="1.4"><path d="M7 9l2-2M6 6l-2 2a2.5 2.5 0 003.5 3.5l2-2M10 10l2-2A2.5 2.5 0 008.5 4.5l-2 2"/></svg></div>
    <div class="abs social" style="left:513px" aria-label="Phone"><svg width="14" height="14" viewBox="0 0 14 14" fill="none" stroke="#fff" stroke-width="1.4"><path d="M2 1h3l1.5 3.5-2 1.2a8 8 0 004 4l1.2-2L13 9v3a1 1 0 01-1 1C6 13 1 8 1 2a1 1 0 011-1z"/></svg></div>
    <div class="abs social" style="left:577px" aria-label="Email"><svg width="16" height="12" viewBox="0 0 16 12" fill="none" stroke="#fff" stroke-width="1.4"><rect x="1" y="1" width="14" height="10" rx="1.5"/><path d="M1.5 2l6.5 5 6.5-5"/></svg></div>
    <div class="abs center copyright">© Copyrights 2018 - The Elder Nook. All Rights Reserved.</div>
  </footer>
</div>
</body>
</html>
```